Upscale business cards needed for Board of Directors

We need professional business cards created for members of our family business Board of Directors. We would like these relatively simple and straightforward, but also with a unique element to set them apart. Probably stick with neutral and simple colors - white, grey etc. We need space for the traditional elements, including name, title, address, email/phone number. And we will be creating several from this template so it needs to be template that is easy to switch information in and out of.
Business
See description

```html
<!DOCTYPE html>
<html lang="en">
<head>
<meta charset="utf-8">
<title>Harborline Holdings – Business Cards</title>
<link rel="stylesheet" href="https://fonts.googleapis.com/css2?family=Open+Sans:wght@400;600&display=swap">
<style>
  :root {
    --bg: #e9e7e3;
    --card-white: #ffffff;
    --ink-dark: #262324;
    --ink-black: #1f1d1e;
    --gold: #b9a57e;
    --gold-light: #c9b792;
    --gold-text: #c0a878;
    --contact-text: #3b372f;
    --white: #ffffff;
  }
  * { box-sizing: border-box; margin: 0; padding: 0; }
  html, body { width: 1200px; height: 950px; overflow: hidden; }
  body {
    background: var(--bg);
    font-family: "Open Sans", Arial, sans-serif;
    position: relative;
  }
  .card {
    position: absolute;
    top: 140px;
    width: 390px;
    height: 670px;
    box-shadow: 0 6px 18px rgba(0,0,0,0.18);
  }
  /* Front card */
  .card-front { left: 160px; background: var(--card-white); }
  .front-column {
    position: absolute;
    left: 62px;
    width: 266px;
    top: 0;
    bottom: 0;
  }
  .identity-block {
    height: 190px;
    background: var(--ink-dark);
    display: flex;
    flex-direction: column;
    align-items: center;
    justify-content: center;
    padding-top: 10px;
  }
  .identity-block svg { width: 22px; height: 24px; margin-bottom: 6px; }
  .person-name {
    color: var(--gold-text);
    font-weight: 600;
    font-size: 17px;
    letter-spacing: 0.5px;
    text-transform: uppercase;
  }
  .person-title {
    color: var(--white);
    font-size: 13px;
    margin-top: 2px;
  }
  .company-name {
    position: absolute;
    left: -40px;
    right: -40px;
    top: 190px;
    height: 92px;
    display: flex;
    align-items: center;
    justify-content: center;
    font-weight: 600;
    font-size: 24px;
    color: var(--ink-black);
  }
  .contact-block {
    position: absolute;
    top: 282px;
    left: 0;
    right: 0;
    bottom: 0;
    background: linear-gradient(180deg, var(--gold-light), var(--gold));
    display: flex;
    flex-direction: column;
    align-items: center;
    padding-top: 28px;
    gap: 18px;
    color: var(--contact-text);
    font-size: 13px;
    text-align: center;
  }
  .contact-item { display: flex; flex-direction: column; align-items: center; gap: 6px; line-height: 1.35; }
  .contact-item svg { width: 14px; height: 14px; fill: var(--ink-dark); }

  /* Back card */
  .card-back {
    left: 650px;
    background: var(--ink-dark);
    display: flex;
    align-items: center;
    justify-content: center;
  }
  .back-company-name {
    font-weight: 600;
    font-size: 30px;
    color: var(--white);
  }
</style>
</head>
<body>
  <section class="card card-front">
    <div class="front-column">
      <div class="identity-block">
        <svg viewBox="0 0 22 24" aria-hidden="true">
          <circle cx="11" cy="7" r="6" fill="#c0a878"/>
          <rect x="2" y="15" width="18" height="9" rx="3" fill="#c0a878"/>
        </svg>
        <div class="person-name">Daniel Hale</div>
        <div class="person-title">CEO/Founder</div>
      </div>
      <div class="company-name">Harborline Holdings</div>
      <div class="contact-block">
        <div class="contact-item">
          <svg viewBox="0 0 14 14" aria-hidden="true"><path d="M7 0a5 5 0 0 0-5 5c0 3.6 5 9 5 9s5-5.4 5-9a5 5 0 0 0-5-5zm0 7a2 2 0 1 1 0-4 2 2 0 0 1 0 4z"/></svg>
          <span>4210 Juniper Court<br>Fairbanks, Alaska 99712</span>
        </div>
        <div class="contact-item">
          <svg viewBox="0 0 14 14" aria-hidden="true"><path d="M3 0.5l2.2 2.8-1.3 1.6c.8 1.8 2.4 3.4 4.2 4.2l1.6-1.3 2.8 2.2-1.2 2.6C6.5 12.6 1.4 7.5 0.4 1.7z"/></svg>
          <span>907 555 0148</span>
        </div>
        <div class="contact-item">
          <svg viewBox="0 0 14 14" aria-hidden="true"><path d="M0 3h14v8H0zM0.8 3.6L7 8l6.2-4.4"/></svg>
          <span>contact@harborline.com</span>
        </div>
        <div class="contact-item">
          <svg viewBox="0 0 14 14" aria-hidden="true"><circle cx="7" cy="7" r="6.5"/></svg>
          <span>www.harborline.com</span>
        </div>
      </div>
    </div>
  </section>

  <section class="card card-back">
    <div class="back-company-name">Harborline Holdings</div>
  </section>
</body>
</html>
```